New Website Design for PHOVAN.org

We are looking for a new website design for PHOVAN.org. PHOVAN is a non profit home inspector association based in California. Home Inspectors are people that come out and look at a house before it's purchased to let the buyer know of any defects that may exist.
Our site is based on Joomla so if you'll be able to make a Joomla 3 template as well, please let us know (not required, but a bonus).
We would like to see designs that incorporate royal blue, white and chrome into the site as that's our main business colors.
We would like a place for rotating banners though they don't need to be the same size as the current site.
We would like navigation to be easier to manage with menus only across the top (via drop down menus) where we are going to sort out the items currently on the side. Possibly the front page could have a graphic link to separate portals for Realtors, Home Buyers and Inspectors, but that's just one option.
We would like a good mobile design or something that will scale easily to mobile.
The Find an Inspector feature is important and should stand out. The ASK PHOVANr site
Current home page feels a bit busy. Would like to simplify a bit.

```html
<!DOCTYPE html>
<html lang="en">
<head>
<meta charset="utf-8">
<title>PHOVAN – Home</title>
<link rel="stylesheet" href="https://fonts.googleapis.com/css2?family=Open+Sans:wght@400;600;700&family=Mulish:wght@300;400&display=swap">
<style>
:root{
  --royal:#1b3a9e;
  --royal-light:#2a5bd8;
  --link-blue:#1640b8;
  --page:#f1f1f1;
  --white:#ffffff;
  --chrome:#e4e4e4;
  --chrome-dark:#cfcfcf;
  --text:#333;
  --muted:#8d8d8d;
  --nav-text:#555;
  --footer:#2b2b2b;
  --footer-deep:#1f1f1f;
  --footer-text:#c9c9c9;
}
*{box-sizing:border-box;margin:0;padding:0}
html,body{width:961px;height:1200px;overflow:hidden}
body{background:var(--page);font-family:"Open Sans",Arial,sans-serif;color:var(--text);position:relative}
.sheet{position:absolute;left:88px;top:0;width:784px;height:1200px;background:var(--white)}
.abs{position:absolute}
/* header */
.brand{left:10px;top:12px;display:flex;align-items:center;gap:8px}
.brand-dot{width:22px;height:22px;border-radius:50%;background:var(--royal)}
.brand-name{font-size:22px;font-weight:700;color:var(--royal);letter-spacing:1px}
.search{left:464px;top:42px;width:173px;height:30px;background:#e6e6e6;border:1px solid #d6d6d6;font-size:9px;color:#666;padding:10px 0 0 11px;letter-spacing:.5px}
.search svg{position:absolute;right:8px;top:7px}
.social{top:45px;display:flex;gap:8px;left:649px}
.social span{width:26px;height:26px;border-radius:3px;display:block}
/* nav */
.nav{left:0;top:104px;width:784px;height:45px;background:linear-gradient(#f6f6f6,var(--chrome));display:flex;align-items:center;font-size:10.5px;color:var(--nav-text)}
.nav a{color:inherit;text-decoration:none;position:absolute;top:16px}
.nav .current{left:0;top:0;width:89px;height:45px;background:linear-gradient(var(--royal-light),var(--royal));color:#fff;text-align:center;padding-top:16px;font-weight:600}
/* banner */
.banner{left:0;top:162px;width:784px;height:284px;background:linear-gradient(90deg,#caa13a 0%,#8a6440 30%,#a7794a 55%,#6d6058 80%,#1c1c1c 100%)}
.shade{left:30px;top:446px;width:724px;height:20px;background:radial-gradient(ellipse at top,rgba(0,0,0,.18),transparent 70%)}
.dots{left:372px;top:457px;display:flex;gap:2px}
.dots i{width:12px;height:12px;border-radius:50%;background:#e6e6e6;display:block}
.dots i.on{background:#777}
/* features */
.feature{top:512px;width:240px}
.feature h2{font-family:"Mulish",sans-serif;font-weight:400;font-size:14.5px;color:var(--link-blue);text-align:center;margin-bottom:20px;letter-spacing:.2px}
.frame{width:242px;height:120px;background:#fff;box-shadow:0 0 4px rgba(0,0,0,.2);padding:8px}
.frame div{width:100%;height:100%}
.feature h3{font-family:"Mulish",sans-serif;font-weight:400;font-size:13.5px;line-height:16px;color:#333;margin:22px 4px 0}
.feature p{font-family:"Mulish",sans-serif;font-size:9.5px;line-height:17px;color:var(--muted);margin:14px 4px 0}
/* welcome */
.welcome{left:14px;top:815px;width:362px}
.welcome h1{font-family:"Mulish",sans-serif;font-weight:300;font-size:20px;color:#555}
.welcome h1 b{color:var(--royal);font-weight:400}
.welcome p{font-family:"Mulish",sans-serif;font-size:9.5px;line-height:16.8px;color:var(--muted);margin-top:6px}
.field{width:179px}
.field label{display:block;font-size:8.5px;color:#444;margin-bottom:3px}
.field span{display:block;height:19px;border:1px solid #d8d8d8;background:linear-gradient(#f0f0f0,#fff)}
.btn{left:586px;top:921px;width:179px;height:21px;border-radius:3px;background:linear-gradient(var(--royal-light),var(--royal));color:#fff;font-size:9px;font-weight:700;text-align:center;line-height:21px}
/* footer */
.footer{left:0;top:970px;width:784px;height:184px;background:repeating-linear-gradient(0deg,rgba(255,255,255,.03) 0 1px,transparent 1px 3px),var(--footer)}
.col{top:24px;color:var(--footer-text);font-size:9.5px;line-height:14.4px}
.col h4{font-size:13.5px;font-weight:400;color:#fff;margin-bottom:13px}
.copy{left:0;top:1154px;width:784px;height:46px;background:var(--footer-deep);border-top:1px solid #3a3a3a;color:#999;font-size:8.5px;text-align:center;line-height:34px}
</style>
</head>
<body>
<div class="sheet">
  <header>
    <div class="abs brand"><span class="brand-dot"></span><span class="brand-name">PHOVAN</span></div>
    <div class="abs search">SEARCH:
      <svg width="16" height="16" viewBox="0 0 16 16"><circle cx="6.5" cy="6.5" r="5" fill="none" stroke="#333" stroke-width="2"/><line x1="10" y1="10" x2="15" y2="15" stroke="#333" stroke-width="2.5"/></svg>
    </div>
    <div class="abs social">
      <span style="background:#1aa0dc"></span><span style="background:#2a8db0"></span><span style="background:#4fb4e6"></span><span style="background:#3a5474"></span>
    </div>
  </header>
  <nav class="abs nav">
    <a class="current" href="#">Home</a>
    <a href="#" style="left:107px">Find an Inspector</a>
    <a href="#" style="left:232px">Home Buyers &amp; Seller</a>
    <a href="#" style="left:378px">Real Estate Agents</a>
    <a href="#" style="left:507px">Inspectors</a>
    <a href="#" style="left:595px">Ask PHOVAN</a>
    <a href="#" style="left:682px">Conferences</a>
  </nav>
  <div class="abs banner" role="img" aria-label="Two home inspectors examining kitchen cabinets"></div>
  <div class="abs shade"></div>
  <div class="abs dots"><i></i><i class="on"></i><i></i></div>

  <section class="abs feature" style="left:10px">
    <h2>PATH TO SUCCESS</h2>
    <div class="frame"><div role="img" aria-label="Red and white growth, success and career arrow illustration" style="background:radial-gradient(circle,#d84040 0%,#e8a0a0 35%,#f4f4f4 60%)"></div></div>
    <h3>Lorem Ipsum is simply dummy text of the printing and typesetting industry.</h3>
    <p>Lorem Ipsum has been the industry's standard dummy text ever since the 1500s, when an unknown printer took a galley of type and</p>
  </section>
  <section class="abs feature" style="left:268px">
    <h2>EDUCATIONAL PUBLICATIONS</h2>
    <div class="frame"><div role="img" aria-label="Open book in front of stacks of books" style="background:linear-gradient(#3a2a20,#8a5a30 45%,#e0c090 70%,#6a3a20)"></div></div>
    <h3>Lorem Ipsum is simply dummy text of the printing and typesetting industry.</h3>
    <p>Lorem Ipsum has been the industry's standard dummy text ever since the 1500s, when an unknown printer took a galley of type and</p>
  </section>
  <section class="abs feature" style="left:525px">
    <h2>ASK PHOVAN</h2>
    <div class="frame"><div role="img" aria-label="Small figure sitting on a red question mark" style="background:radial-gradient(circle at 50% 65%,#d42020 0%,#e88080 22%,#f4f4f4 45%)"></div></div>
    <h3>Lorem Ipsum is simply dummy text of the printing and typesetting industry.</h3>
    <p>Lorem Ipsum has been the industry's standard dummy text ever since the 1500s, when an unknown printer took a galley of type and</p>
  </section>

  <section class="abs welcome">
    <h1>Welcome to a <b>PHOVAN</b></h1>
    <p>Lorem Ipsum is simply dummy text of the printing and typesetting industry. Lorem Ipsum has been the industry's standard dummy text ever since the 1500s, when an unknown printer took a galley of type and scrambled it to make a type specimen book.Lorem Ipsum is simply dummy text of the printing and typesetting industry. Lorem Ipsum. has been the industry's standard dummy text ever since the 1500s, when an unknown printer.</p>
  </section>
  <div class="abs field" style="left:396px;top:832px"><label>First Name :</label><span></span></div>
  <div class="abs field" style="left:586px;top:832px"><label>Email Address :</label><span></span></div>
  <div class="abs field" style="left:396px;top:867px"><label>Last Name :</label><span></span></div>
  <div class="abs field" style="left:586px;top:867px"><label>Phone Number :</label><span></span></div>
  <div class="abs field" style="left:396px;top:906px"><label style="font-size:9.5px">Enter Zip Code or Country</label><span></span></div>
  <div class="abs btn">SEARCH INSPECTOR</div>

  <footer class="abs footer">
    <div class="abs col" style="left:16px;width:160px"><h4>Popular</h4>Inspection FAQs<br>Common Venting of Gas<br>Becoming a Member<br>Education / CECs<br>Affiliate Directory</div>
    <div class="abs col" style="left:199px;width:215px"><h4>Business method</h4>Ma quande lingues coalesce, li grammatica del resultant lingue es plu simplic e regulari quam ti del coalescent lingues. Li nov lingua franca va esser plu simplic e regulari quam li existent Europan lingues.</div>
    <div class="abs col" style="left:466px;width:160px"><h4>Get in touch</h4>2400 Elm Street &nbsp;Suite 110<br>Riverton CA 95000-1234<br>Hours: M-F, 8:00am - 5:00pm<br>Phone: (800) 555-0142 or<br>(916) 555-0187<br>Fax: (916) 555-0163<br>Webmaster@PHOVAN.ORG</div>
    <div class="abs col" style="left:668px;width:110px"><h4>Who We are</h4>Established in 1976, PHOVAN is a non-profit trade association, with chapters located throughout the state. PHOVAN is a member-driven,</div>
  </footer>
  <div class="abs copy">Copyright © 2013 PHOVAN. All rights reserved.</div>
</div>
</body>
</html>
```